Business Card Design

Electronic Security Installation Specialists

Check out our website at www.tallbrookllc.com to see what we do.

Industry/Entity Type

Business

Contact Information for Business Card

Tall Brook
Marjorie Hadley
281 Orchard Rise
Mapleton, WV 25871

Colors
3176b5
0455a3
ffffff

```html
<!DOCTYPE html>
<html lang="en">
<head>
<meta charset="utf-8">
<title>Tall Brook – Business Card</title>
<link rel="stylesheet" href="https://fonts.googleapis.com/css2?family=Open+Sans:wght@400;600;700&display=swap">
<style>
  :root {
    --brand-blue: #3176b5;
    --brand-deep: #0455a3;
    --white: #ffffff;
    --card-black: #0b0b0c;
    --ink: #3a3a3a;
    --muted: #5a5a5a;
    --stage: #e9e7e3;
  }
  * { box-sizing: border-box; margin: 0; padding: 0; }
  html, body {
    width: 1200px; height: 913px; overflow: hidden;
    background: var(--stage);
    font-family: "Open Sans", Arial, sans-serif;
  }
  .stage {
    position: relative; width: 1200px; height: 913px;
    display: flex; align-items: center; justify-content: center; gap: 60px;
  }
  .card {
    width: 500px; height: 286px; border-radius: 4px;
    box-shadow: 0 6px 18px rgba(0,0,0,.18);
    position: relative;
  }
  .card--front {
    background: var(--card-black);
    display: flex; align-items: center; justify-content: center;
  }
  .wordmark { display: flex; align-items: center; gap: 14px; }
  .wordmark__dot {
    width: 44px; height: 44px; border-radius: 50%;
    background: var(--brand-blue);
  }
  .wordmark__name {
    font-weight: 700; font-size: 34px; letter-spacing: .5px;
  }
  .card--front .wordmark__name { color: var(--white); }
  .card--back {
    background: var(--white);
    display: flex; align-items: center;
    padding: 0 30px 0 34px;
  }
  .card--back .wordmark { width: 220px; }
  .card--back .wordmark__dot { width: 40px; height: 40px; }
  .card--back .wordmark__name { color: var(--brand-deep); font-size: 28px; }
  .contact { margin-left: 16px; color: var(--ink); }
  .contact__name {
    color: var(--brand-blue); font-weight: 700; font-size: 19px; line-height: 1.15;
  }
  .contact__title { color: var(--muted); font-size: 13px; margin-bottom: 26px; }
  .contact__address { font-size: 12.5px; line-height: 1.4; margin-bottom: 8px; }
  .contact__list { list-style: none; font-size: 12.5px; line-height: 1.55; }
  .contact__list li { display: flex; align-items: center; gap: 8px; }
  .contact__list svg { width: 11px; height: 11px; fill: var(--brand-deep); flex: none; }
  .contact__web { color: var(--brand-blue); }
</style>
</head>
<body>
<main class="stage">
  <section class="card card--front" aria-label="Card front">
    <div class="wordmark">
      <span class="wordmark__dot"></span>
      <span class="wordmark__name">Tall Brook</span>
    </div>
  </section>

  <section class="card card--back" aria-label="Card back">
    <div class="wordmark">
      <span class="wordmark__dot"></span>
      <span class="wordmark__name">Tall Brook</span>
    </div>
    <div class="contact">
      <p class="contact__name">Marjorie Hadley</p>
      <p class="contact__title">Managing Director</p>
      <p class="contact__address">281 Orchard Rise<br>Mapleton, WV 25871</p>
      <ul class="contact__list">
        <li>
          <svg viewBox="0 0 16 16" aria-hidden="true"><path d="M3 1l3 3-1.5 2a9 9 0 0 0 5.5 5.5L12 10l3 3-2 2C7 15 1 9 1 3z"/></svg>
          304-555-0182
        </li>
        <li>
          <svg viewBox="0 0 16 16" aria-hidden="true"><circle cx="8" cy="8" r="7" fill="none" stroke="#0455a3" stroke-width="1.6"/><path d="M1 8h14M8 1c3 3 3 11 0 14M8 1c-3 3-3 11 0 14" fill="none" stroke="#0455a3" stroke-width="1.2"/></svg>
          m.hadley@tallbrookllc.com
        </li>
        <li class="contact__web">
          <svg viewBox="0 0 16 16" aria-hidden="true"><path d="M1 3h14v10H1z"/><path d="M1 3l7 6 7-6" fill="none" stroke="#fff" stroke-width="1.3"/></svg>
          www.tallbrookllc.com
        </li>
      </ul>
    </div>
  </section>
</main>
</body>
</html>
```